Business card for event manager / organizer "waiter service"

Draft of a new valuable business card for my company.
Events, personnel service providers, festivals

```html
<!DOCTYPE html>
<html lang="de">
<head>
<meta charset="UTF-8">
<title>Berkhoff Servicewerk – Visitenkarte</title>
<link href="https://fonts.googleapis.com/css2?family=Poppins:wght@400;500;600;700;800&display=swap" rel="stylesheet">
<style>
  :root {
    --page-bg: #d9d3cc;
    --card-bg: #eee9e3;
    --card-edge: #f7f3ee;
    --accent: #d8742c;
    --ink: #2f2c2a;
    --text: #55504b;
    --photo-top: #d8cfc6;
    --photo-mid: #9b938c;
    --photo-low: #3a3634;
  }
  * { margin: 0; padding: 0; box-sizing: border-box; }
  html, body {
    width: 1200px; height: 1047px; overflow: hidden;
    background: var(--page-bg);
    font-family: "Poppins", sans-serif;
  }
  .card {
    position: absolute; left: 151px; top: 289px;
    width: 947px; height: 518px;
    background: linear-gradient(135deg, var(--card-edge), var(--card-bg));
    border-radius: 22px;
    overflow: hidden;
    box-shadow: 0 10px 40px rgba(0,0,0,0.12);
  }
  .brand {
    position: absolute; left: 38px; top: 37px;
    display: flex; align-items: center; gap: 12px;
  }
  .brand-mark { width: 80px; height: 80px; background: var(--accent); }
  .brand-name {
    font-weight: 800; font-size: 22px; line-height: 1.1;
    color: var(--ink); letter-spacing: 0.3px;
  }
  .brand-tagline {
    position: absolute; left: 130px; top: 119px;
    font-size: 9.5px; color: var(--text);
  }
  .person-name {
    position: absolute; left: 38px; top: 176px;
    font-weight: 600; font-size: 33px; line-height: 1.2; color: var(--accent);
  }
  .person-role {
    position: absolute; left: 38px; top: 224px;
    font-size: 21px; line-height: 1.2; color: var(--text);
  }
  .contact-list {
    position: absolute; left: 38px; top: 279px;
    list-style: none;
  }
  .contact-list li {
    display: flex; align-items: center; gap: 9px;
    height: 34.5px; font-size: 22px; color: var(--text);
  }
  .contact-list svg { width: 19px; height: 19px; flex: none; fill: var(--accent); }
  .portrait {
    position: absolute; left: 529px; top: 43px;
    width: 383px; height: 475px;
    background: linear-gradient(180deg, var(--photo-top) 0%, var(--photo-mid) 45%, var(--photo-low) 100%);
    border-radius: 180px 180px 0 0;
  }
</style>
</head>
<body>
  <div class="card">
    <div class="brand">
      <div class="brand-mark"></div>
      <div class="brand-name">BERKHOFF<br>SERVICEWERK</div>
    </div>
    <p class="brand-tagline">..weil jedes Fest gute Gastgeber verdient!</p>

    <h1 class="person-name">Jonas Berkhoff</h1>
    <p class="person-role">Inhaber</p>

    <ul class="contact-list">
      <li><svg viewBox="0 0 24 24"><path d="M3 9c0-3 4-5 9-5s9 2 9 5v2h-5V9H8v2H3z"/><path d="M6 12h12l2 8H4z"/></svg>02361 555 12 40</li>
      <li><svg viewBox="0 0 24 24"><path d="M3 9c0-3 4-5 9-5s9 2 9 5v2h-5V9H8v2H3z"/><path d="M6 12h12l2 8H4z"/></svg>0170 555 48 21</li>
      <li><svg viewBox="0 0 24 24"><circle cx="12" cy="12" r="10"/><path d="M7 8h5v4H8zM13 14h4v4h-4z" fill="#eee9e3"/></svg>www.berkhoff-servicewerk.de</li>
      <li><svg viewBox="0 0 24 24"><path d="M2 6h20v13H2z"/><path d="M2 6l10 7 10-7" fill="none" stroke="#eee9e3" stroke-width="2"/></svg>info@berkhoff-servicewerk.de</li>
      <li><svg viewBox="0 0 24 24"><path d="M12 2a7 7 0 0 0-7 7c0 5 7 13 7 13s7-8 7-13a7 7 0 0 0-7-7z"/><circle cx="12" cy="9" r="3" fill="#eee9e3"/></svg>Lindenweg 14, 45699 Herten</li>
      <li><svg viewBox="0 0 24 24"><rect x="3" y="3" width="18" height="18" rx="3"/></svg>www.treffpunkt.net/berkhoffservice</li>
    </ul>

    <div class="portrait" role="img" aria-label="Porträtfoto des Inhabers in Hemd und Weste mit verschränkten Armen"></div>
  </div>
</body>
</html>
```